Homemaking training schools needs a Business Card design

Designer, Hello!

No special requirements, good-looking enough.
--------------------------------------------------------------------------

Name: Marcus Dole
Chairman
Tel: 0574-71948263
Mobile: 13857420916
Email: kelvora@mailnest.example
Web: www.prt2019.example
Add: No.258, LanpingJie, BeiyuanQu, Ningbo, Zhejiang

LOGO
Ningbo PRT Homemaking Training School

Target Market(s)

pregnant women, mothers, infants, the elderly and families, including cleaning, cooking, nursing training.

Industry/Entity Type

Business

Contact Information for Business Card

Name: Marcus Dole
Chairman
Tel: 0574-71948263
Mobile: 13857420916
Email: kelvora@mailnest.example
Web: www.prt2019.example

LOGO

Font styles to use
Serif
Sans Serif
Decorative

Requirements
Nice to have
• Feels: clean, specifications, safety, comfort, warmth and happiness.

```html
<!DOCTYPE html>
<html lang="en">
<head>
<meta charset="utf-8">
<title>PinRuiTing Business Card</title>
<link href="https://fonts.googleapis.com/css2?family=Montserrat:wght@500;600;700&family=Source+Sans+3:wght@400&display=swap" rel="stylesheet">
<style>
  :root {
    --brand-blue: #1b75bc;
    --brand-pink: #e6007e;
    --ink: #4a4a4a;
    --rule: #cfcfcf;
    --bar-grey: #8c8c8c;
    --card: #ffffff;
    --backdrop: #5b5b5b;
  }
  * { margin: 0; padding: 0; box-sizing: border-box; }
  html, body {
    width: 1105px; height: 1200px; overflow: hidden;
    background: var(--backdrop);
  }
  .card {
    position: absolute;
    left: 196px;
    width: 720px; height: 412px;
    background: var(--card);
  }
  .card--front { top: 146px; }
  .card--back { top: 602px; }

  .brand {
    position: absolute;
    display: flex;
    align-items: center;
    transform: translate(-50%, -50%);
    white-space: nowrap;
  }
  .brand-name {
    font-family: "Montserrat", sans-serif;
    font-weight: 600;
    color: var(--brand-blue);
    line-height: 1;
  }
  .brand-dot {
    flex: none;
    border-radius: 50%;
    background: var(--brand-pink);
  }
  .card--front .brand { left: 199px; top: 228px; gap: 10px; }
  .card--front .brand-name { font-size: 38px; }
  .card--front .brand-dot { width: 14px; height: 14px; }
  .card--back .brand { left: 360px; top: 242px; gap: 16px; }
  .card--back .brand-name { font-size: 62px; }
  .card--back .brand-dot { width: 22px; height: 22px; }

  .divider {
    position: absolute; left: 373px; top: 91px;
    width: 1px; height: 246px; background: var(--rule);
  }
  .contact {
    position: absolute; left: 403px; top: 88px;
    font-family: "Source Sans 3", sans-serif;
    color: var(--ink);
  }
  .contact-name {
    font-family: "Montserrat", sans-serif;
    font-weight: 600; font-size: 27px; color: var(--brand-blue);
    line-height: 34px;
  }
  .contact-title {
    font-family: "Montserrat", sans-serif;
    font-weight: 700; font-size: 19px; color: var(--brand-pink);
    line-height: 24px; margin-bottom: 14px;
  }
  .contact-address { font-size: 19px; line-height: 27px; margin-bottom: 6px; }
  .contact-list { list-style: none; font-size: 19px; line-height: 28px; }
  .contact-list li { display: flex; align-items: center; gap: 10px; }
  .contact-list svg { width: 17px; height: 17px; flex: none; fill: var(--brand-blue); }

  .accent-bar {
    position: absolute; left: 0; bottom: 0; width: 720px; height: 9px;
    display: flex; gap: 3px;
  }
  .accent-bar span { display: block; height: 100%; }
  .accent-bar .grey { width: 545px; background: var(--bar-grey); }
  .accent-bar .blue { width: 56px; background: var(--brand-blue); }
  .accent-bar .pink { width: 53px; background: var(--brand-pink); }
  .accent-bar .blue-end { flex: 1; background: var(--brand-blue); }
</style>
</head>
<body>
  <section class="card card--front">
    <div class="brand"><span class="brand-dot"></span><span class="brand-name">PinRuiTing</span></div>
    <div class="divider"></div>
    <div class="contact">
      <div class="contact-name">Marcus Dole</div>
      <div class="contact-title">Chairman</div>
      <div class="contact-address">No.258, LanpingJie<br>BeiyuanQu, Ningbo, Zhejiang</div>
      <ul class="contact-list">
        <li><svg viewBox="0 0 24 24"><path d="M6.6 10.8a15.1 15.1 0 0 0 6.6 6.6l2.2-2.2c.3-.3.7-.4 1-.2 1.1.4 2.300.6 3.600.6.6 0 1 .4 1 1V20c0 .6-.4 1-1 1C10.6 21 3 13.4 3 4c0-.6.4-1 1-1h3.5c.6 0 1 .4 1 1 0 1.3.2 2.5.6 3.6.1.3 0 .7-.2 1z"/></svg>0574-71948263</li>
        <li><svg viewBox="0 0 24 24"><path d="M7 1h10a2 2 0 0 1 2 2v18a2 2 0 0 1-2 2H7a2 2 0 0 1-2-2V3a2 2 0 0 1 2-2zm0 3v14h10V4zm5 15.5a1.2 1.2 0 1 0 0 2.4 1.2 1.2 0 0 0 0-2.4z"/></svg>13857420916</li>
        <li><svg viewBox="0 0 24 24"><path d="M2 5h20v14H2zm2 2v.4l8 5.2 8-5.2V7zm0 2.8V17h16V9.8l-8 5.2z"/></svg>kelvora@mailnest.example</li>
        <li><svg viewBox="0 0 24 24"><path d="M12 2a10 10 0 1 0 0 20 10 10 0 0 0 0-20zm-1 17.9A8 8 0 0 1 4.1 11H7l2 2v2l2 2zm6.9-2.5A2 2 0 0 0 16 16h-1v-3l-4-4H9V7h2l2-2V4.3a8 8 0 0 1 4.9 13.1z"/></svg>www.prt2019.example</li>
      </ul>
    </div>
    <div class="accent-bar">
      <span class="grey"></span><span class="blue"></span><span class="pink"></span><span class="blue-end"></span>
    </div>
  </section>

  <section class="card card--back">
    <div class="brand"><span class="brand-dot"></span><span class="brand-name">PinRuiTing</span></div>
  </section>
</body>
</html>
```